tinyTally Resource Book - 10 maths tasks to do outside

I need a 22 (11 pages back to back) page A6 sized book produced to standard for submission to professional printer. Needs to be as .pdf file showing guide lines and allowances for colour bleed. I have text already written and submitted as attachment in a Word file with margins set to A6 size. The theme of the materials is "Nature Play" so using lots of pictures from nature (Australia preferably) and showing lots of patterns in nature (rocks, leaves, flower petals etc). Some of the tasks refer to specific activities, such as "shadows" and "floating" so would be great to illustrate appropriately. The big emphasis is on learning outside the classroom, getting kids to engage actively with nature. I would like to see the pages as full colour - so not white background. The book itself will be spiral bound along the top edge so a margin of at least 1cm will be required at the top of each page (or the bottom of even numbered pages). Book will be printed on plastic laminated matte paper for outdoor use. Font size needs to be big enough to read. Fonts sizes, alignments and page numbers are all different at the moment and need to be standardised. One photo is included in a page as a sample if you can use it, otherwise disregard. Logo for Wattlebrook Numeracy Guild is also included to have as part of the acknowledgements at the back of the book.

Target Market(s)

Book is for early childhood and preschool teachers.

Industry/Entity Type

Education

Font styles to use
Sans Serif

Requirements
Must have
• Colour and appeal.
Nice to have
• Use of natural colours instead of bright catchy colours but that is your call.
Should not have
• American spelling

```html
<!DOCTYPE html>
<html lang="en-AU">
<head>
<meta charset="utf-8">
<title>tinyTally – 4. One More</title>
<link rel="stylesheet" href="https://fonts.googleapis.com/css2?family=Jost:wght@400;500;700;800&display=swap">
<style>
  :root {
    --paper: #ffffff;
    --trim-mark: #3b3b3b;
    --wood-light: #e8c491;
    --wood-mid: #dcb07a;
    --wood-deep: #cf9f68;
    --heading-navy: #2b3990;
    --heading-outline: #ffffff;
    --bullet-red: #d2323a;
    --body-ink: #3c3835;
    --leaf-light: #c9e36a;
    --leaf-mid: #8fc644;
    --badge-navy: #2b3990;
  }
  * { margin: 0; padding: 0; box-sizing: border-box; }
  html, body { width: 892px; height: 1200px; overflow: hidden; background: var(--paper); }
  .sheet { position: relative; width: 892px; height: 1200px; background: var(--paper); font-family: "Jost", sans-serif; }
  .crop-marks { position: absolute; inset: 0; }
  .page {
    position: absolute; left: 54px; top: 56px; width: 784px; height: 1090px;
    background:
      repeating-linear-gradient(90deg, rgba(255,255,255,0.08) 0 14px, rgba(160,110,60,0.07) 14px 22px, rgba(255,255,255,0) 22px 41px),
      linear-gradient(180deg, var(--wood-light), var(--wood-mid) 55%, var(--wood-deep));
  }
  .leaf-sprig {
    position: absolute; left: 512px; top: 874px; width: 196px; height: 168px; border-radius: 50%;
    background: radial-gradient(ellipse at 50% 50%, var(--leaf-light), var(--leaf-mid) 60%, rgba(143,198,68,0) 72%);
  }
  .section-heading {
    position: absolute; left: 124px; color: var(--heading-navy); font-weight: 800;
    font-size: 45px; line-height: 52px; letter-spacing: 0.3px; white-space: nowrap;
    text-shadow: 2px 0 0 var(--heading-outline), -2px 0 0 var(--heading-outline), 0 2px 0 var(--heading-outline), 0 -2px 0 var(--heading-outline),
                 2px 2px 0 var(--heading-outline), -2px 2px 0 var(--heading-outline), 2px -2px 0 var(--heading-outline), -2px -2px 0 var(--heading-outline),
                 3px 4px 5px rgba(0,0,0,0.35);
  }
  .task-title { font-size: 50px; line-height: 56px; top: 140px; }
  .task-list { position: absolute; left: 218px; list-style: none; color: var(--body-ink); font-size: 30px; line-height: 36px; font-weight: 400; letter-spacing: 0.8px; white-space: nowrap; }
  .task-list li { position: relative; }
  .task-list li::before {
    content: ""; position: absolute; left: -28px; top: 11px; width: 15px; height: 15px;
    background: var(--bullet-red); transform: rotate(45deg);
  }
  .steps { top: 199px; }
  .prompts-heading { top: 332px; }
  .prompts { top: 388px; }
  .variations-heading { top: 556px; }
  .variations { top: 613px; }
  .big-ideas-heading { top: 890px; }
  .big-ideas { top: 946px; }
  .page-number { position: absolute; left: 696px; top: 1024px; width: 72px; height: 72px; }
</style>
</head>
<body>
<div class="sheet">
  <svg class="crop-marks" width="892" height="1200" viewBox="0 0 892 1200" aria-hidden="true">
    <g stroke="var(--trim-mark)" stroke-width="1">
      <line x1="74" y1="0" x2="74" y2="52"/><line x1="0" y1="74" x2="52" y2="74"/>
      <line x1="818" y1="0" x2="818" y2="52"/><line x1="840" y1="74" x2="892" y2="74"/>
      <line x1="74" y1="1148" x2="74" y2="1200"/><line x1="0" y1="1126" x2="52" y2="1126"/>
      <line x1="818" y1="1148" x2="818" y2="1200"/><line x1="840" y1="1126" x2="892" y2="1126"/>
    </g>
  </svg>

  <div class="page" role="img" aria-label="Light bamboo wood grain background"></div>
  <div class="leaf-sprig" role="img" aria-label="Two sprigs of fresh green leaves"></div>

  <h1 class="section-heading task-title">4. One More</h1>
  <ul class="task-list steps">
    <li>Make a line of objects</li>
    <li>Ask partner to make a line of similar<br>objects “and one more”</li>
  </ul>

  <h2 class="section-heading prompts-heading">Prompting questions</h2>
  <ul class="task-list prompts">
    <li>Can you make a line that uses the<br>same number of objects as the first line<br>but it is longer? shorter? (by changing<br>the spacing between objects)</li>
  </ul>

  <h2 class="section-heading variations-heading">Variations</h2>
  <ul class="task-list variations">
    <li>Make a line that is “one less”, “two<br>more”</li>
    <li>Make more lines of the same number<br>of objects beneath the first line to make<br>a rectangle</li>
    <li>Change orientation of line from hori-<br>zontal to vertical or diagonal</li>
  </ul>

  <h2 class="section-heading big-ideas-heading">Big Ideas</h2>
  <ul class="task-list big-ideas">
    <li>One-to-one<br>correspondence</li>
    <li>Equivalence</li>
    <li>More than, less than</li>
  </ul>

  <svg class="page-number" viewBox="0 0 72 72" aria-label="Page 9">
    <polygon points="36,2 70,27 57,69 15,69 2,27" fill="var(--badge-navy)"/>
    <text x="36" y="52" text-anchor="middle" font-family="Jost, sans-serif" font-size="30" font-weight="500" fill="#ffffff">9</text>
  </svg>
</div>
</body>
</html>
```